National appliance rental company needs a newspaper ad design

We need an ad template that we can use for different newspaper advertising. Ad is to be colourful - I have attached our current marketing so you have an idea of colours.
Text to be something like the below:

Want it, Rent it, Own it!

Need to update your furniture? Kids need stuff for school?

(Put in pics of phones and TV)

Zelvos starting from just $8 per week
Smart phones starting from $10 per week
Large family fridges from $30 per week

TV’s, laptops, whitegoods, furniture, beds – we will finance just about anything!

Fast approvals – call 1300 582 967 or go to www.brightwellhomeleasing.com.au/apply - NOW!
$50 credit voucher given to the first 10 successful applicants.

(Pic of logo somewhere)
Terms and conditions apply. Pricing based on 24 month term

Brightwell Home Leasing P/L ACN 061 847 293. Australian Credit Licence # 718294

Target Market(s)

Low income people and families

Industry/Entity Type

Appliance

Requirements
Must have
• I would love to have a couple of different sizes.
• Maybe 6cm x 10 cm, and also 10cms x 10cms.
Nice to have
• Please use the green from fridge magnet and colours from our logo, etc.

```html
<!DOCTYPE html>
<html lang="en">
<head>
<meta charset="utf-8">
<title>Brightwell Home Leasing – Newspaper Ad</title>
<link rel="stylesheet" href="https://fonts.googleapis.com/css2?family=Arimo:ital,wght@0,400;0,700;1,400&family=Fredoka:wght@600;700&display=swap">
<style>
  :root {
    --page-bg: #4a3424;
    --sun-core: #fbb040;
    --sun-mid: #f47b20;
    --sun-edge: #d7261e;
    --brand-red: #e2231a;
    --brand-blue: #0b72b5;
    --brand-green: #6ab43e;
    --voucher-yellow: #fdc70f;
    --ink: #231f20;
    --white: #ffffff;
  }
  * { box-sizing: border-box; margin: 0; padding: 0; }
  html, body { width: 1200px; height: 1000px; overflow: hidden; }
  body { background: var(--page-bg); font-family: "Arimo", Arial, sans-serif; position: relative; }

  .ad {
    position: absolute; left: 118px; top: 18px; width: 967px; height: 967px;
    overflow: hidden;
    background: radial-gradient(ellipse at 45% 42%, #fde58a 0%, var(--sun-core) 22%, var(--sun-mid) 55%, var(--sun-edge) 100%);
  }
  .ad > * { position: absolute; }

  .mascot-art {
    left: 62px; top: 17px; width: 170px; height: 210px; border-radius: 14px;
    background: linear-gradient(180deg, #f4f4f4, #cfd3d6);
  }
  .brand-name {
    left: 240px; top: 70px; width: 360px; text-align: center;
    font-family: "Arimo", Arial, sans-serif; font-weight: 700; font-size: 42px; line-height: 46px;
    color: var(--brand-red);
  }
  .brand-tagline {
    left: 240px; top: 208px; width: 360px; text-align: center;
    font-style: italic; font-size: 19px; color: var(--ink);
  }
  .phones-art {
    left: 632px; top: 17px; width: 310px; height: 210px; border-radius: 16px;
    background: linear-gradient(135deg, #e9eef2 0%, #3a3d42 50%, #1d9bd7 100%);
  }
  .tv-art {
    left: 657px; top: 197px; width: 300px; height: 280px; border-radius: 6px;
    background: linear-gradient(160deg, #2b2d31, #050506);
  }

  .headline {
    left: 20px; top: 272px; width: 660px; text-align: center;
    font-family: "Fredoka", "Arial Rounded MT Bold", sans-serif; font-weight: 700;
    font-size: 82px; line-height: 86px; color: var(--brand-red);
    -webkit-text-stroke: 4px var(--white); paint-order: stroke fill;
    text-shadow: 2px 3px 4px rgba(0,0,0,.35);
  }
  .prompt {
    left: 60px; top: 472px; width: 500px; height: 64px; text-align: center;
    padding-top: 8px;
    background: linear-gradient(90deg, rgba(255,255,255,0) 0%, rgba(255,255,255,.55) 30%, rgba(255,255,255,.55) 70%, rgba(255,255,255,0) 100%);
    font-weight: 700; font-size: 19px; line-height: 25px; color: var(--ink);
  }

  .offer-box {
    top: 550px; height: 236px; background: var(--brand-blue);
    border: 3px solid var(--white); border-radius: 14px; color: var(--white);
  }
  .offer-box--prices { left: 22px; width: 324px; padding: 12px 0 0 19px; font-size: 26px; line-height: 31px; }
  .offer-box--prices p { margin-bottom: 13px; }
  .offer-box--prices strong { color: var(--voucher-yellow); }
  .offer-box--range { left: 368px; width: 306px; padding-top: 16px; text-align: center; font-size: 26px; line-height: 31px; }

  .voucher {
    left: 624px; top: 476px; width: 420px; height: 420px; border-radius: 50%;
    background: var(--voucher-yellow); border: 4px solid var(--white);
  }
  .voucher-text {
    left: 668px; top: 562px; width: 300px; text-align: center;
    font-weight: 700; font-size: 36px; line-height: 40px; color: var(--brand-red);
  }

  .approvals-band {
    left: 0; top: 800px; width: 967px; height: 88px; background: var(--brand-green); text-align: center;
  }
  .approvals-title {
    display: block; padding-top: 10px;
    font-weight: 700; font-size: 35px; line-height: 38px; color: var(--brand-red);
    -webkit-text-stroke: 3px var(--white); paint-order: stroke fill;
  }
  .approvals-line { font-size: 21px; line-height: 30px; color: var(--ink); }
  .approvals-line strong { font-weight: 700; }

  .legal {
    left: 0; top: 906px; width: 967px; text-align: center;
    font-weight: 700; font-size: 19px; line-height: 24px; color: var(--white);
  }
</style>
</head>
<body>
  <div class="ad">
    <div class="mascot-art" role="img" aria-label="Cartoon fridge mascot pointing at the brand name"></div>
    <div class="brand-name">Brightwell Home Leasing</div>
    <div class="brand-tagline">“It’s cheaper to go straight to us!”</div>
    <div class="phones-art" role="img" aria-label="Three smartphones fanned out"></div>
    <div class="tv-art" role="img" aria-label="Flat screen television"></div>

    <h1 class="headline">Want it, Rent it,<br>Own it!</h1>
    <p class="prompt">Need to update your furniture?<br>Kids need stuff for school?</p>

    <div class="offer-box offer-box--prices">
      <p>Zelvos starting from<br>just <strong>$8</strong> per week</p>
      <p>Smart phones starting<br>from <strong>$10</strong> per week</p>
      <p>Large family fridges<br>from <strong>$30</strong> per week</p>
    </div>
    <div class="voucher"></div>
    <div class="offer-box offer-box--range">TV’s, laptops,<br>whitegoods,<br>furniture, beds –<br>we will finance<br>just about<br>anything!</div>
    <p class="voucher-text">$50 credit voucher given to the first 10 successful applicants.</p>

    <div class="approvals-band">
      <strong class="approvals-title">FAST APPROVALS</strong>
      <p class="approvals-line">call <strong>1300 582 967</strong> or go to www.brightwellhomeleasing.com.au/apply - <strong>NOW!</strong></p>
    </div>

    <p class="legal">Terms and conditions apply. Pricing based on 24 month term<br>Brightwell Home Leasing P/L ACN 061 847 293. Australian Credit Licence # 718294</p>
  </div>
</body>
</html>
```